Local massage therapist needs some new marketing material

Hi there! I am a massage therapist here in Denver, CO in Alder Bend(shopping and art district) of the city. My business is called Lumo Bodywork of Denver. My practice has an eastern influence and I do reflexology, thai massage and use Chinese herbs, etc. I know all my clients and pay close attention to details. I am also very respectful of tradition and it shows in how I work. I tend to like modern, clean, fun, Asian designs. I am wanting a new business card and brochure. I have a logo and branding for my business that I want used in the design. Currently, the sign for my building is purple and I think my logo was designed to be purple. I will attach pictures of it and can send whatever files are necessary so it can be integrated into the brochure, etc. I like the purple but open to using other colors as well. Thanks!
My website is lumobodyworkofdenver.example where info can be gathered about me and services/fees for brochure.
Updates

Just increased budget. Please see new feedback in discussion thread.

Thanks!

                                       HEY ALL,

Just wanted to let you know that I made a change to my website. It is on the Prices Page. I no longer have the frequent  flyer prices but I added discounts. Let me know if you have any questions. Thanks so much!

Target Market(s)

healthy, urban, educated, upper middle class, yogis

Industry/Entity Type

Marketing

Requirements
Must have
• logo stays purple
Should not have
• not too busy

```html
<!DOCTYPE html>
<html lang="en">
<head>
<meta charset="utf-8">
<title>Lumo Bodywork of Denver – Business Card</title>
<link rel="stylesheet" href="https://fonts.googleapis.com/css2?family=Open+Sans:ital,wght@0,400;0,600;0,700;1,400&family=Josefin+Sans:wght@400&display=swap">
<style>
  :root {
    --purple: #662d91;
    --ink: #3a3a3a;
    --stripe: #2f2f2f;
    --rule: #b8b8b8;
    --card: #ffffff;
    --stage: #e9e9ee;
  }
  * { box-sizing: border-box; margin: 0; padding: 0; }
  html, body { width: 1200px; height: 987px; overflow: hidden; }
  body {
    background: var(--stage);
    font-family: "Open Sans", Arial, sans-serif;
    color: var(--ink);
    position: relative;
  }
  .card {
    position: absolute;
    left: 240px;
    width: 720px;
    height: 400px;
    background: var(--card);
    border-radius: 28px;
    overflow: hidden;
    box-shadow: 0 6px 18px rgba(0,0,0,0.12);
  }
  .card--front { top: 70px; }
  .card--back { top: 517px; }

  /* Front */
  .front-wave { position: absolute; inset: 0; }
  .brand {
    position: absolute;
    left: 40px;
    top: 38px;
    width: 270px;
    text-align: center;
  }
  .brand__mark {
    width: 56px; height: 56px;
    border-radius: 50%;
    background: var(--purple);
    margin: 0 auto 10px;
  }
  .brand__name {
    font-family: "Josefin Sans", "Open Sans", sans-serif;
    font-weight: 400;
    font-size: 70px;
    letter-spacing: 5px;
    color: var(--purple);
    line-height: 1;
  }
  .divider {
    position: absolute;
    left: 330px; top: 54px;
    width: 1px; height: 136px;
    background: var(--rule);
  }
  .contact {
    position: absolute;
    left: 348px; top: 56px;
    list-style: none;
    font-size: 17px;
    line-height: 30px;
    white-space: nowrap;
  }
  .contact li { display: flex; align-items: center; gap: 8px; }
  .contact svg { width: 15px; height: 15px; flex: none; }
  .contact .address { margin-top: 6px; }
  .holder {
    position: absolute;
    right: 56px; bottom: 16px;
    text-align: right;
    color: #fff;
  }
  .holder__name { font-size: 28px; font-weight: 600; line-height: 1.15; }
  .holder__title { font-size: 18px; line-height: 1.3; }

  /* Back */
  .appointment {
    position: absolute;
    inset: 34px 48px 30px 48px;
  }
  .appointment__title {
    text-align: center;
    color: var(--purple);
    font-weight: 700;
    font-size: 19px;
    letter-spacing: 0.5px;
    margin-bottom: 18px;
  }
  .field { display: flex; align-items: flex-end; gap: 8px; font-size: 17px; margin-bottom: 18px; }
  .field__line { flex: 1; border-bottom: 1px dotted #888; height: 18px; }
  .field__unit { font-size: 19px; }
  .hours { margin-top: 22px; font-size: 20px; line-height: 29px; text-align: center; }
  .note { margin-top: 14px; font-size: 18px; font-style: italic; color: #666; text-align: center; }
</style>
</head>
<body>

<section class="card card--front" aria-label="Business card front">
  <svg class="front-wave" viewBox="0 0 720 400" width="720" height="400" aria-hidden="true">
    <path d="M0,190 C260,200 480,240 720,300" fill="none" stroke="var(--purple)" stroke-width="3"/>
    <path d="M0,206 C260,218 480,258 720,310 L720,318 C480,270 260,240 0,236 Z" fill="var(--stripe)"/>
    <path d="M0,248 C260,256 480,286 720,328 L720,400 L0,400 Z" fill="var(--purple)"/>
  </svg>

  <div class="brand">
    <div class="brand__mark"></div>
    <div class="brand__name">LUMO</div>
  </div>

  <div class="divider"></div>

  <ul class="contact">
    <li>
      <svg viewBox="0 0 16 16"><circle cx="8" cy="8" r="8" fill="var(--purple)"/><path d="M5.3 4.2l1.4 1.6-.8 1a5 5 0 0 0 2.3 2.3l1-.8 1.6 1.4-.8 1.3C7.6 11 5 8.4 4 5z" fill="#fff"/></svg>
      303.555.0148
    </li>
    <li>
      <svg viewBox="0 0 16 16"><rect x="1" y="3" width="14" height="10" rx="1.5" fill="var(--purple)"/><path d="M2 4.5l6 4.5 6-4.5" fill="none" stroke="#fff" stroke-width="1.3"/></svg>
      info@lumobodyworkofdenver.example
    </li>
    <li>
      <svg viewBox="0 0 16 16"><circle cx="8" cy="8" r="7" fill="var(--purple)"/><g fill="none" stroke="#fff" stroke-width="1"><ellipse cx="8" cy="8" rx="3" ry="7"/><path d="M1 8h14M2.5 4.5h11M2.5 11.5h11"/></g></svg>
      www.lumobodyworkofdenver.example
    </li>
    <li class="address">1450 E Alder Ave, Denver, CO 80206</li>
  </ul>

  <div class="holder">
    <div class="holder__name">Your Name</div>
    <div class="holder__title">Title</div>
  </div>
</section>

<section class="card card--back" aria-label="Business card back">
  <div class="appointment">
    <h2 class="appointment__title">YOUR APPOINTMENT</h2>
    <div class="field"><span>Name :</span><span class="field__line"></span></div>
    <div class="field">
      <span>Date :</span><span class="field__line"></span>
      <span>Time :</span><span class="field__line"></span>
      <span class="field__unit">am / pm</span>
    </div>
    <p class="hours">Tues - Fri 10am - 8pm Sat 10am-5pm<br>(Appointments required) No walk-ins please.</p>
    <p class="note">We appreciate a 24 hr. notice for cancellations</p>
  </div>
</section>

</body>
</html>
```